Etiketten-Design für einen importierten Honig
Zielgruppe
Wir importieren originalen Manuka Honig aus Neuseeland. Der Manuka Honig ist bekannt für seine besonderen Eigenschaften (antibakteriell, etc.). Ein Glas unseres Honigs (500g) kostet zwischen 30 und 150 EUR.
Unsere Zielgruppe sind gesundheitsbewusste Kunden, die wenig preissensibel sind. Überwiegend wird der Manuka Honig im Fachhandel (z.B. Reformhaus, Drogerie, Biomarkt, etc.) verkauft. Der Großteil unserer Kunden ist 30+ Jahre.
Aufgabenstellung
Bei dem Etikett handelt es sich um das erste Produktetikett. Damit ist in der Farbgestaltung noch alles offen. Das Logo und der Name ist jedoch fix.
Das Etikett ist wird auf einem bpa-freien schwarzen Plastikbehälter angebracht. Dieser ist bei Manuka Honigen Standard aufgrund des langen Transports von Neuseeland nach Deutschland (gerne googeln). Der Deckel dieses Behälters ist schwarz.
Nachdem es sich um ein hochpreisiges Produkt handelt, soll das Etikett diese hohe Wertigkeit widerspiegeln. Damit ist eine Veredelung des Etiketts notwendig. Viele Konkurrenten arbeiten mit Gold, alternative Farben sind jedoch auch möglich.
Das Etikett überdeckt drei der vier Seiten des Plastikbehälters (vorne + links + rechts). Die Maße sind 160 mm x 60 mm. Zusätzlich zu den Etikettenmaßen bitte 2 mm Beschnittzugabe je Seite hinzufügen.
Hintergrundinformationen zu unserer Marke:
- Der Markenname lautet Kalvio. Der Markenname leitet sich von der ersten Imkerin Neuseelands ab - Edith Carrow. Sie hatte im Jahr 1839 die ersten Bienenstöcke nach Neuseeland gebracht und den ersten Manuka Honig geerntet.
- Unser Logo ist eine Verbindung einer Frau und den neuseeländischen Farn. Dieses Logo stellt also direkt eine Verbindung zu Neuseeland dar.
- Unsere Marke Kalvio ist eine qualitativ hochwertige, luxuriöse und hochpreisige Marke. Genau wie in dem Logo selbst, sollen diese Verbindungen zu Neuseeland, der Natur (Honig ist ein Naturprodukt) und Edith Carrow auch auf dem Etikett zu finden sein.
Wonach suchen wir:
- Wir sind auf der Suche nach einem einzigartigen Design, der unseren Honig besonders hervorhebt. Das Etikett soll auffällig sein und uns von anderen unterscheiden. (Eye-catching)
- Eine Veredelung des Etiketts ist Pflicht, da dies für uns die Wertigkeit des Etiketts und des Produktes stark erhöht. In welcher Art die Veredelung durchgeführt wird, ist Ihnen überlassen.
Das dürfen Sie frei wählen:
- Bisher haben..

```html
<!DOCTYPE html>
<html lang="de">
<head>
<meta charset="utf-8">
<title>Kalvio Manuka Honig – Etikett</title>
<link rel="stylesheet" href="https://fonts.googleapis.com/css2?family=Lilita+One&family=Roboto:wght@400;700&display=swap">
<style>
  :root {
    --backdrop: #d6aa6f;
    --paper: #e5e2dd;
    --paper-shade: #dcd8d1;
    --copper-dark: #c07558;
    --copper-light: #eaa88b;
    --gold: #b8823f;
    --cream: #ece4d4;
  }
  html, body {
    margin: 0;
    width: 1200px;
    height: 1200px;
    overflow: hidden;
    background: var(--backdrop);
  }
  .canvas {
    position: relative;
    width: 1200px;
    height: 1200px;
  }
  .label {
    position: absolute;
    left: 100px;
    top: 157px;
    width: 1000px;
    height: 887px;
    background: radial-gradient(ellipse at 40% 40%, var(--paper), var(--paper-shade));
  }
  .label svg { display: block; }
  .product-word {
    font-family: "Lilita One", "Arial Black", sans-serif;
    fill: url(#copper);
  }
  .strength {
    font-family: "Lilita One", "Arial Black", sans-serif;
    fill: var(--cream);
  }
  .brand-name {
    font-family: "Roboto", Arial, sans-serif;
    font-weight: 700;
    fill: var(--gold);
  }
  .brand-mark {
    fill: none;
    stroke: var(--gold);
    stroke-width: 6;
  }
  .origin-line {
    font-family: "Roboto", Arial, sans-serif;
    font-weight: 400;
    fill: var(--gold);
  }
</style>
</head>
<body>
<main class="canvas">
  <section class="label">
    <svg width="1000" height="887" viewBox="0 0 1000 887">
      <defs>
        <linearGradient id="copper" x1="0" y1="0" x2="1" y2="0.3">
          <stop offset="0" stop-color="var(--copper-dark)"/>
          <stop offset="0.55" stop-color="var(--copper-dark)"/>
          <stop offset="1" stop-color="var(--copper-light)"/>
        </linearGradient>
      </defs>

      <g class="product-name">
        <text class="product-word" x="56" y="297" font-size="350" textLength="536" lengthAdjust="spacingAndGlyphs">MA</text>
        <text class="product-word" x="56" y="573" font-size="350" textLength="430" lengthAdjust="spacingAndGlyphs">NU</text>
        <text class="product-word" x="56" y="849" font-size="350" textLength="432" lengthAdjust="spacingAndGlyphs">KA</text>
        <text class="strength" transform="translate(112 836) rotate(-90)" font-size="78" textLength="232" lengthAdjust="spacingAndGlyphs">450<tspan font-size="48" dy="-26">+</tspan></text>
      </g>

      <g class="brand">
        <circle class="brand-mark" cx="812" cy="360" r="128"/>
        <text class="brand-name" x="947" y="576" font-size="58" text-anchor="end" textLength="272" lengthAdjust="spacingAndGlyphs">KALVIO</text>
      </g>

      <g class="origin">
        <text class="origin-line" x="947" y="636" font-size="40" text-anchor="end" textLength="311" lengthAdjust="spacing">HONIG AUS</text>
        <text class="origin-line" x="947" y="689" font-size="40" text-anchor="end" textLength="364" lengthAdjust="spacing">NEUSEELAND</text>
        <text class="origin-line" x="947" y="741" font-size="40" text-anchor="end" textLength="136" lengthAdjust="spacing">500G</text>
      </g>
    </svg>
  </section>
</main>
</body>
</html>
```